Software Product Flyer Design

A established czech software company needs a marketing flyer to promote their software product and its modules.
The overall feel of the flyer must to be serious, but also eye-catching, enticing, clever and bold to attract customers.
Unifying graphic element is the new product logo.
The flyer would be A4, colour both sides and folded once (to give 4 pages of A5).
Title page - product logo with module name and module icon, short presentation of the product and list of its key features.
Inside pages - detailed informations with screenshots or graphical schemas.
Back side - informations about technical requirements and user support, contacts (address, phone, fax, e-mail, web pages - no social networks).
Product logo, module icon and some images attached.
Updates
Hello,
Reason: For organizational reasons we extending the deadline by 10 days.
FYI: We have uploaded the new ZIP file with previous version of our flyer.
Attached PDF file with text for inner pages.
Target Market(s)
Existing or new customers like municipalities, public authorities and nonprofit organizations.
Industry/Entity Type
Marketing
Requirements
Must have
- Winning designer must provide a template for Adobe InDesign based on his graphic design.
Avoid to using exotic fonts - in Czech we use Latin Extended characters (like áéěíýůčřžšťďň).
Nice to have
- Using graphic motif from product logo like as attached splash screen.

```html
<!DOCTYPE html>
<html lang="en">
<head>
<meta charset="utf-8">
<title>Norvix – Module Flyer</title>
<link rel="stylesheet" href="https://fonts.googleapis.com/css2?family=Questrial&display=swap">
<style>
  :root {
    --page: #ffffff;
    --stage: #e8e5e1;
    --ink: #2f3236;
    --ink-soft: #3c3f44;
    --band-dark: #17181a;
    --band-mid: #2e3034;
    --panel: #474b52;
    --orange: #f26a2e;
    --orange-deep: #e2531b;
    --text-light: #f2f2f2;
    --fold: #d9d9d9;
  }
  * { box-sizing: border-box; margin: 0; padding: 0; }
  html, body { width: 1200px; height: 889px; overflow: hidden; }
  body {
    background: var(--stage);
    font-family: "Questrial", "Century Gothic", sans-serif;
    position: relative;
  }
  .spread {
    position: absolute; left: 6px; top: 25px;
    width: 1188px; height: 838px;
    background: var(--page);
    box-shadow: 0 2px 10px rgba(0,0,0,.18);
    overflow: hidden;
  }
  .page { position: absolute; top: 0; height: 838px; width: 594px; }
  .page--back { left: 0; }
  .page--front { left: 594px; border-left: 1px solid var(--fold); }

  /* back page */
  .back-band { position: absolute; left: 0; top: 0; }
  .brand-mark {
    position: absolute; left: 98px; top: 86px;
    display: flex; align-items: center; gap: 12px;
    font-size: 40px; color: var(--ink); letter-spacing: 0.5px;
  }
  .brand-mark__square { width: 22px; height: 22px; background: var(--orange); border-radius: 5px; }
  .contacts {
    position: absolute; left: 268px; top: 100px;
    font-size: 16px; line-height: 20px; color: var(--ink);
  }
  .address {
    position: absolute; left: 111px; top: 186px;
    font-size: 16px; color: var(--ink);
  }
  .support { position: absolute; left: 53px; top: 436px; width: 500px; }
  .support__title { font-size: 24px; color: var(--orange); font-weight: 400; margin-bottom: 6px; letter-spacing: .3px; }
  .support__body { font-size: 15px; line-height: 31px; color: var(--text-light); padding-left: 5px; }

  /* front page */
  .front-brand {
    position: absolute; left: 170px; top: 58px;
    display: flex; align-items: center; gap: 16px;
    font-size: 64px; line-height: 1; color: var(--ink-soft);
  }
  .front-brand__square { width: 30px; height: 30px; background: var(--orange); border-radius: 7px; }
  .front-panel {
    position: absolute; left: 0; top: 184px;
    width: 572px; height: 524px;
    background: var(--panel);
    border-radius: 0 30px 30px 0;
    box-shadow: 8px 14px 22px rgba(0,0,0,.22);
  }
  .module-art {
    position: absolute; left: 0; top: 113px;
    width: 544px; height: 260px;
    background: linear-gradient(90deg, #5a4a22 0%, #3f6b26 35%, #5f8d2c 60%, #c8d6ea 78%, #f0a51c 100%);
    border-radius: 0 40px 40px 0;
    opacity: .9;
  }
  .module-label {
    position: absolute; left: 144px; top: 428px;
    width: 302px; height: 47px; border-radius: 24px;
    background: linear-gradient(180deg, #ff8a4a 0%, var(--orange) 45%, var(--orange-deep) 100%);
    color: #fff; font-size: 29px; letter-spacing: 5px;
    text-align: center; line-height: 47px;
    box-shadow: 0 3px 4px rgba(0,0,0,.25);
  }
  .module-label__reflection {
    position: absolute; left: 144px; top: 477px;
    width: 302px; height: 22px; border-radius: 0 0 24px 24px;
    background: linear-gradient(180deg, rgba(0,0,0,.25), rgba(0,0,0,0));
  }
  .website {
    position: absolute; left: 264px; top: 786px;
    font-size: 21px; letter-spacing: 4px; color: var(--ink);
  }
</style>
</head>
<body>
<main class="spread">
  <section class="page page--back">
    <svg class="back-band" width="594" height="838" viewBox="0 0 594 838" aria-hidden="true">
      <defs>
        <linearGradient id="bandShade" x1="0" y1="1" x2="1" y2="0">
          <stop offset="0" stop-color="#17181a"/>
          <stop offset="1" stop-color="#3a3c40"/>
        </linearGradient>
      </defs>
      <polygon points="0,427 594,188 594,705 267,838 0,838" fill="url(#bandShade)"/>
    </svg>

    <div class="brand-mark"><span class="brand-mark__square"></span>norvix</div>

    <div class="contacts">
      <p>P : 012 - 456 - 7890</p>
      <p>F : 012 - 456 - 7890</p>
      <p>E :&nbsp; info@norvix.com</p>
    </div>
    <p class="address">Suite 000 Cityname, Countryname 0000 00</p>

    <article class="support">
      <h2 class="support__title">USER SUPPORT</h2>
      <p class="support__body">Lorem ipsum dolor sit amet, consectetuer adipiscing elit, sed diam nonummy nibh euismod tincidunt ut laoreet dolore magna aliquam erat volutpat. Ut wisi enim ad minim veniam, quis nostrud exerci tation ullamcorper suscipit lobortis nisl ut aliquip ex ea commodo consequat. Duis autem vel eum iriure dolor in hendrerit in vulputate velit esse molestie consequat, vel illum dolore eu feugiat nulla facilisis at vero eros et accumsan et iusto odio dignissim qui blandit praesent luptatum zzril delenit augue duis dolore te feugait nulla facilisi.</p>
    </article>
  </section>

  <section class="page page--front">
    <div class="front-brand"><span class="front-brand__square"></span>norvix</div>

    <div class="front-panel">
      <div class="module-art" role="img" aria-label="Module illustration: circuit-textured hand pointing at a notebook icon with a letter A and a yellow pencil"></div>
      <div class="module-label">module name</div>
      <div class="module-label__reflection"></div>
    </div>

    <p class="website">www.norvix.com</p>
  </section>
</main>
</body>
</html>
```